Business Card Design

Our Pharmacy Opens late - the last to close in Brisbane
over 30 years since opened.
Open from 7am - 11pm every day.
Next to Corbel 7 Day Medical Centre
Parking in front of shop
Sit with a pharmacist for every script - the best advice every time.
Private consulting room.
We have the medication that you need.
Wide range Home Health Care products.

Looking for a card that my (young) staff feel happy to hand out to people they they meet.
Updates

Hello Many thanks for your submissions I just need to clarify the costings for this project as per my updated brief Please confirm then we can proceed Many thanks Clive

Reason: due to the adjusted brief and query I have extended the deadline Many thanks for those that have submitted, I will choose the designer as soon as I understand the costings of the project, as per the message despatched today Regards clive

Target Market(s)

men and women 30-70

Industry/Entity Type

Business

Contact Information for Business Card

Meltons Pharmacy - Corbel
317 Galloway Rd
Corbel 4187
Last to Close
Open 7am - 11pm

Font styles to use
Sans Serif

Requirements
Must have
• each batch of 250 will have the following staff names

Doreen Vallow, Senior Pharmacist
Lucia Tomba, Pharmacist
Wu Lan, Pharmacist
Odalie Brunskill, Pharmacist
Greta Lounds, Retail Manager
Joy Mettrick, Marketing Manager
Clive Melton, Pharmacist Proprietor
Should not have
• Please advise if the cost of this job covers the 7 individualised business cards.

Each staff member needs their own card.

please advise

```html
<!DOCTYPE html>
<html lang="en">
<head>
<meta charset="utf-8">
<title>Meltons Pharmacy – Business Card</title>
<link href="https://fonts.googleapis.com/css2?family=Open+Sans:wght@400;600;700&display=swap" rel="stylesheet">
<style>
  :root {
    --navy: #1f2a78;
    --blue-light: #6f7fd0;
    --yellow: #e3dc1c;
    --yellow-soft: #f4f07a;
    --white: #ffffff;
    --ink: #2b2b2b;
    --ink-soft: #444444;
    --page: #e9e6e0;
  }
  * { box-sizing: border-box; margin: 0; padding: 0; }
  html, body { width: 1200px; height: 865px; overflow: hidden; }
  body {
    background: var(--page);
    font-family: "Open Sans", Arial, sans-serif;
    color: var(--ink);
    position: relative;
  }
  .card {
    position: absolute;
    width: 660px;
    height: 377px;
    left: 270px;
    overflow: hidden;
    box-shadow: 0 6px 18px rgba(0,0,0,0.18);
  }
  .card--front { top: 32px; background: radial-gradient(ellipse at 65% 75%, var(--yellow-soft), var(--yellow) 70%); }
  .card--back  { top: 455px; background: radial-gradient(ellipse at 50% 50%, var(--yellow-soft), var(--yellow) 75%); }

  /* front */
  .front__top {
    position: absolute; left: 0; top: 0; width: 100%; height: 200px;
    background: var(--white);
  }
  .front__rule {
    position: absolute; left: 0; top: 200px; width: 100%; height: 9px;
    background: linear-gradient(var(--blue-light) 0 3px, var(--navy) 3px 9px);
  }
  .brand {
    position: absolute; left: 34px; top: 30px;
    display: flex; align-items: center; gap: 12px;
  }
  .brand__dot { width: 46px; height: 46px; border-radius: 50%; background: var(--navy); flex: none; }
  .brand__name {
    font-weight: 700; font-size: 27px; line-height: 1.1; color: var(--navy);
  }
  .person {
    position: absolute; right: 34px; top: 26px; text-align: right;
  }
  .person__name { font-weight: 700; font-size: 24px; line-height: 1.3; letter-spacing: 0.5px; text-transform: uppercase; color: var(--ink); }
  .person__role { font-size: 16px; line-height: 1.3; color: #555; }
  .address {
    position: absolute; left: 34px; top: 136px;
    display: flex; align-items: center; gap: 10px;
    font-size: 16px; line-height: 1.3; color: var(--ink-soft);
  }
  .contact {
    position: absolute; display: flex; flex-direction: column; gap: 20px;
    font-size: 17px; font-weight: 600; color: var(--ink);
  }
  .contact--left { left: 58px; top: 250px; }
  .contact--right { left: 360px; top: 250px; }
  .contact__item { display: flex; align-items: center; gap: 12px; line-height: 1.3; }
  .icon { width: 18px; height: 18px; flex: none; }

  /* back */
  .stripe { position: absolute; top: 0; height: 100%; }
  .stripe--navy { width: 14px; background: var(--navy); }
  .stripe--light { width: 6px; background: var(--blue-light); }
  .stripe--l1 { left: 40px; } .stripe--l2 { left: 60px; }
  .stripe--r1 { right: 40px; } .stripe--r2 { right: 60px; }
  .hours {
    position: absolute; left: 0; top: 0; width: 100%; height: 100%;
    display: flex; flex-direction: column; align-items: center; justify-content: center; gap: 6px;
    text-align: center; color: var(--navy);
  }
  .hours__headline { font-weight: 700; font-size: 34px; line-height: 1.2; text-transform: uppercase; letter-spacing: 1px; }
  .hours__times { font-weight: 600; font-size: 20px; line-height: 1.3; color: var(--ink); }
</style>
</head>
<body>

<section class="card card--front" aria-label="Business card front">
  <div class="front__top"></div>
  <div class="front__rule"></div>

  <div class="brand">
    <span class="brand__dot"></span>
    <span class="brand__name">Meltons<br>Pharmacy</span>
  </div>

  <div class="person">
    <p class="person__name">Clive Melton</p>
    <p class="person__role">Pharmacist Proprietor</p>
  </div>

  <div class="address">
    <svg class="icon" viewBox="0 0 24 24" aria-hidden="true"><path fill="#444" d="M12 2a7 7 0 0 0-7 7c0 5 7 13 7 13s7-8 7-13a7 7 0 0 0-7-7zm0 9.5A2.5 2.5 0 1 1 12 6.5a2.5 2.5 0 0 1 0 5z"/></svg>
    <span>317 Galloway Rd<br>Corbel 4187</span>
  </div>

  <div class="contact contact--left">
    <p class="contact__item">
      <svg class="icon" viewBox="0 0 24 24" aria-hidden="true"><rect x="6" y="2" width="12" height="20" rx="2" fill="none" stroke="#2b2b2b" stroke-width="2"/><circle cx="12" cy="18" r="1.2" fill="#2b2b2b"/></svg>
      0412 555 038
    </p>
    <p class="contact__item">
      <svg class="icon" viewBox="0 0 24 24" aria-hidden="true"><g fill="none" stroke="#2b2b2b" stroke-width="1.8"><circle cx="12" cy="12" r="9"/><ellipse cx="12" cy="12" rx="4" ry="9"/><path d="M3 12h18M5 7h14M5 17h14"/></g></svg>
      www.meltonsrx.com
    </p>
  </div>

  <div class="contact contact--right">
    <p class="contact__item">
      <svg class="icon" viewBox="0 0 24 24" aria-hidden="true"><path fill="#2b2b2b" d="M6.6 10.8a15 15 0 0 0 6.6 6.6l2.2-2.2a1 1 0 0 1 1-.25 11.4 11.4 0 0 0 3.6.57 1 1 0 0 1 1 1V20a1 1 0 0 1-1 1A17 17 0 0 1 3 4a1 1 0 0 1 1-1h3.5a1 1 0 0 1 1 1c0 1.25.2 2.45.57 3.6a1 1 0 0 1-.25 1z"/></svg>
      07 3555 0147
    </p>
    <p class="contact__item">
      <svg class="icon" viewBox="0 0 24 24" aria-hidden="true"><path fill="#2b2b2b" d="M2 5h20v14H2z"/><path fill="none" stroke="#e3dc1c" stroke-width="1.6" d="M2.5 5.5 12 13l9.5-7.5"/></svg>
      hello@meltonsrx.com
    </p>
  </div>
</section>

<section class="card card--back" aria-label="Business card back">
  <span class="stripe stripe--navy stripe--l1"></span>
  <span class="stripe stripe--light stripe--l2"></span>
  <span class="stripe stripe--navy stripe--r1"></span>
  <span class="stripe stripe--light stripe--r2"></span>
  <div class="hours">
    <p class="hours__headline">Last to Close</p>
    <p class="hours__times">Open 7am – 11pm</p>
  </div>
</section>

</body>
</html>
```